KVB Website

We need a website for a company based in Doha Qatar called Brightpath Talent Global. It is a global recruitment company, that specializes in both mass recruitment and headhunting. The company is the number 1 one stop shop for recruitment in Qatar. It recruits from all over the world Europe, Asia, Americas, Middle East, Africa for Qatar.

Target Market(s)

Multinational companies, fortune 500 company CEO's, any top earning companies that are looking for a large number of employees or headhunting employees.
Also for candidates looking for companies to work in Qatar.

Industry/Entity Type

Shop

Colors
ffffff

Requirements
Must have
• Most important qualities the website needs to have:
Clean
Modern
Elegant
Professional
Less Tabs
Minimalisitc

Some examples, I would like you to follow are here:
http://www.velmora.ca/
http://www.trovenkip.com/
https://quelbrandix.com/match#

The main color should be white and it has to have a very stylish, modern and cool look. While being minimalistic. I do not want too many tabs. I want it to be simplistic to understand. the only place where the pink logo color is should be in the logo. The logo color should not be anywhere else. It has to be absolutely sleek. Please follow the example websites that I have provided.

I will send the contact details you need to add later. There is no need for a log in page.

Whatever you think that may be important for a recruitment site do suggest. But there is no need for a log in area as we are a different kind of recruitment company.

There should be an area for testimonials from clients. There should also be an area for news flash for the latest countries we are hiring from and the latest companies we are hiring for and the latest positions we are looking for.

Show me the best please. Whoever gives me the best, I will give them an order for the 2nd website too.

Nice to have
• I have included a powerpoint to explain more!

```html
<!DOCTYPE html>
<html lang="en">
<head>
<meta charset="utf-8">
<title>Brightpath Talent Global</title>
<link rel="stylesheet" href="https://fonts.googleapis.com/css2?family=Open+Sans:wght@300;400;600;700&display=swap">
<style>
:root{
  --brand:#a3166a;
  --heading:#3a3a3c;
  --link:#2f2f31;
  --nav-top:#4a4b4e;
  --nav-bottom:#2e2f31;
  --nav-active:#6a6b6e;
  --text:#666;
  --text-dark:#333;
  --band:#f3f3f3;
  --footer-top:#3c3d40;
  --footer-bottom:#1d1e20;
  --footer-base:#151516;
  --footer-text:#e6e6e6;
  --accent-blue:#2b8fe0;
  --white:#fff;
}
*{box-sizing:border-box;margin:0;padding:0}
html,body{width:685px;height:1200px;overflow:hidden;background:var(--white)}
body{position:relative;font-family:'Open Sans',Arial,sans-serif;color:var(--text)}
.abs{position:absolute}

/* header */
.brand{left:50px;top:30px;display:flex;align-items:center;gap:6px}
.brand-dot{width:12px;height:12px;border-radius:50%;background:var(--brand)}
.brand-name{font-size:12px;font-weight:700;color:var(--brand);line-height:1.15;width:110px}
.util{right:51px;top:38px;display:flex;gap:5px;font-size:11px;color:var(--text-dark);align-items:center}
.search{left:486px;top:74px;width:148px;height:20px;border:1px solid #ccc;font-size:8px;color:#888;padding:4px 7px}
.search svg{position:absolute;right:5px;top:4px}

/* nav */
.nav{left:50px;top:117px;width:584px;height:33px;background:linear-gradient(var(--nav-top),var(--nav-bottom));display:flex}
.nav a{color:var(--white);font-size:10px;font-weight:600;text-decoration:none;line-height:33px;padding:0 19px;border-right:1px solid rgba(0,0,0,.25)}
.nav a.active{background:var(--nav-active)}

/* hero */
.hero{left:50px;top:150px;width:584px;height:292px;background:linear-gradient(100deg,#e9e6e3 0%,#c9b8ad 30%,#d8cfc7 55%,#b9c2cf 80%,#e5e5e8 100%)}
.caption{left:66px;top:342px;width:437px;height:66px;background:rgba(40,40,40,.7);padding:8px 16px}
.caption h1{font-size:20px;font-weight:400;color:var(--white);letter-spacing:-.7px;white-space:nowrap;line-height:26px}
.caption p{font-size:10.5px;font-weight:600;color:var(--white);margin-top:3px;letter-spacing:-.2px;white-space:nowrap}
.dots{left:556px;top:419px;display:flex;gap:6px}
.dots i{width:10px;height:10px;border-radius:50%;background:rgba(120,120,120,.75)}

/* columns */
.col-title{font-size:17px;font-weight:400;color:var(--heading)}
.about-img{left:50px;top:514px;width:165px;height:87px;background:linear-gradient(120deg,#f1f1f1,#c9c9c9 50%,#8a8480);border:1px solid #ddd}
.about-text{left:50px;top:614px;width:176px;font-size:8.5px;line-height:16.5px}
.jobs{left:256px;top:508px;width:180px;list-style:none}
.jobs li{position:relative;padding-left:20px;height:41.5px}
.jobs li b{display:block;font-weight:400;font-size:9px;color:var(--link)}
.jobs li span{display:block;font-size:8.5px;margin-top:4px}
.jobs li svg{position:absolute;left:0;top:2px}
.news{left:459px;top:512px;width:180px}
.news-item{border-bottom:1px dotted #aaa;padding-bottom:12px;margin-bottom:13px}
.news-item:last-child{border:none}
.news-item h3{font-size:8.5px;font-weight:400;color:var(--link)}
.news-item time{display:block;font-size:7.5px;margin-top:9px}
.news-item p{font-size:8.5px;line-height:14.5px;color:#555;margin-top:3px}

/* testimonials */
.band{left:0;top:699px;width:685px;height:165px;background:var(--band)}
.arrows{left:614px;top:722px}
.avatar{width:66px;height:66px;border-radius:50%;border:3px solid var(--white);box-shadow:0 0 0 1px #ddd;background:linear-gradient(#d8dde2,#7c8690)}
.quote{width:194px;height:67px;background:var(--white);border:1px solid #ddd;font-family:Arial,Helvetica,sans-serif;font-style:italic;font-size:7.5px;line-height:16.5px;color:#555;padding:8px 13px}
.quote::before{content:"";position:absolute;left:-5px;top:28px;width:8px;height:8px;background:var(--white);border-left:1px solid #ddd;border-bottom:1px solid #ddd;transform:rotate(45deg)}

/* featured */
.partner{top:929px;width:129px;height:38px;border:1px solid #ccc;display:flex;align-items:center;justify-content:center;font-size:10px;font-weight:600;color:var(--text-dark)}

/* footer */
.footer{left:0;top:1006px;width:685px;height:152px;background:linear-gradient(var(--footer-top),var(--footer-bottom))}
.footer-base{left:0;top:1158px;width:685px;height:42px;background:var(--footer-base);border-top:1px solid #333}
.fcol{top:1032px;color:var(--footer-text)}
.fcol h4{font-size:9px;font-weight:700;margin-bottom:6px;font-family:Arial,sans-serif}
.fcol a{display:block;font-size:8.5px;color:var(--footer-text);text-decoration:none;line-height:16.5px}
.newsletter{left:480px;top:1030px;width:160px;color:var(--white)}
.newsletter h4{font-size:12px;font-weight:400}
.newsletter p{font-size:7.8px;font-weight:600;line-height:16.5px;margin-top:4px;letter-spacing:-.2px}
.field{left:480px;top:1088px;width:154px;height:19px;background:var(--white)}
.subscribe{left:565px;top:1118px;width:69px;height:21px;background:var(--accent-blue);color:var(--white);font-size:9px;text-align:center;line-height:21px}
.copy{left:50px;top:1173px;font-size:8px;color:var(--footer-text);font-family:Arial,sans-serif}
.social{left:534px;top:1171px;display:flex;gap:5px}
.social i{width:17px;height:17px;border-radius:50%;background:#8a8a8a}
</style>
</head>
<body>

<header>
  <div class="abs brand"><span class="brand-dot"></span><span class="brand-name">BRIGHTPATH TALENT GLOBAL</span></div>
  <div class="abs util">
    <svg width="11" height="10" viewBox="0 0 11 10"><path d="M0 0h11v7H4l-3 3V7H0z" fill="#333"/></svg><span>Chat</span>
  </div>
  <div class="abs search">Search..
    <svg width="9" height="9" viewBox="0 0 9 9"><circle cx="3.6" cy="3.6" r="2.8" stroke="#999" fill="none" stroke-width="1.2"/><path d="M5.7 5.7 8.5 8.5" stroke="#999" stroke-width="1.4"/></svg>
  </div>
</header>

<nav class="abs nav">
  <a class="active">HOME</a><a>ABOUT US</a><a>SERVICES</a><a>PICTURE GALLERY</a><a>NEWS</a><a>JOB SEARCH</a>
</nav>

<section>
  <div class="abs hero" role="img" aria-label="Smiling businesswoman in front of colleagues at a meeting table"></div>
  <div class="abs caption">
    <h1>Duis autem vel eum iriure dolor in hendrerit</h1>
    <p>Typi non habent claritatem insitam; est usus legentis in iis qui facit</p>
  </div>
  <div class="abs dots"><i></i><i></i><i></i><i></i></div>
</section>

<section>
  <h2 class="abs col-title" style="left:50px;top:476px">About Us</h2>
  <div class="abs about-img" role="img" aria-label="Team of colleagues in a bright office discussion"></div>
  <p class="abs about-text">Our next wave of projects have been acqu ird during 2010 and 2011 and include a nu mbeof retail and residential developments.</p>

  <h2 class="abs col-title" style="left:256px;top:476px">Recent Jobs</h2>
  <ul class="abs jobs">
    <li><svg width="12" height="12" viewBox="0 0 12 12"><circle cx="6" cy="6" r="6" fill="#999"/><path d="M5 3.5 7.5 6 5 8.5" stroke="#fff" fill="none" stroke-width="1.3"/></svg><b>Web Designer ( For Freshers )</b><span>Our next wavie of prijects have been</span></li>
    <li><svg width="12" height="12" viewBox="0 0 12 12"><circle cx="6" cy="6" r="6" fill="#999"/><path d="M5 3.5 7.5 6 5 8.5" stroke="#fff" fill="none" stroke-width="1.3"/></svg><b>Web Designer ( For Freshers )</b><span>Our next wavie of prijects have been</span></li>
    <li><svg width="12" height="12" viewBox="0 0 12 12"><circle cx="6" cy="6" r="6" fill="#999"/><path d="M5 3.5 7.5 6 5 8.5" stroke="#fff" fill="none" stroke-width="1.3"/></svg><b>Web Designer ( For Freshers )</b><span>Our next wavie of projects have been</span></li>
    <li><svg width="12" height="12" viewBox="0 0 12 12"><circle cx="6" cy="6" r="6" fill="#999"/><path d="M5 3.5 7.5 6 5 8.5" stroke="#fff" fill="none" stroke-width="1.3"/></svg><b>Web Designer ( For Freshers )</b><span>Our next wavie of projects have been</span></li>
  </ul>

  <h2 class="abs col-title" style="left:460px;top:476px">News &amp; Events</h2>
  <div class="abs news">
    <article class="news-item"><h3>TYPI NON HABENT CLARITATEM INSITAM;</h3><time>26/11/2013</time><p>Typi non habent claritatem insitam; est len tis in iis qui facit eorum claritatem.</p></article>
    <article class="news-item"><h3>TYPI NON HABENT CLARITATEM INSITAM;</h3><time>26/11/2013</time><p>Typi non habent claritatem insitam; est islen tis in iis qui facit eorum claritatem.</p></article>
  </div>
</section>

<section>
  <div class="abs band"></div>
  <h2 class="abs col-title" style="left:51px;top:716px">Testimonials</h2>
  <svg class="abs arrows" width="22" height="14" viewBox="0 0 22 14"><path d="M7 1 2 7l5 6M15 1l5 6-5 6" stroke="#666" fill="none" stroke-width="1.5"/></svg>
  <div class="abs avatar" style="left:49px;top:761px" role="img" aria-label="Portrait of a client"></div>
  <div class="abs quote" style="left:134px;top:762px">Nullam risus nisi, blandit a convalli vehiculaimin per, purus ut imperdiet luctus, arcu fels accuem elementum non, tempor ac velit. Phasellus.</div>
  <div class="abs avatar" style="left:355px;top:761px" role="img" aria-label="Portrait of a client"></div>
  <div class="abs quote" style="left:440px;top:762px">Nullam risus nisi, blandit a convalli vehiculaimin per, purus ut imperdiet luctus, arcu fels accuem elementum non, tempor ac velit. Phasellus.</div>
</section>

<section>
  <h2 class="abs col-title" style="left:49px;top:884px">Featured Employees</h2>
  <div class="abs partner" style="left:50px">Marwen Holding</div>
  <div class="abs partner" style="left:201px">Solvane Hotels</div>
  <div class="abs partner" style="left:356px">Aerivo Air</div>
  <div class="abs partner" style="left:506px">Castellan Resorts</div>
</section>

<footer>
  <div class="abs footer"></div>
  <div class="abs fcol" style="left:50px"><h4>Nam libertempor</h4><a>Typi non haben</a><a>Successful Campaigns</a><a>New Campaigns</a><a>Ending Soon</a><a>Most Funded Campaigns</a></div>
  <div class="abs fcol" style="left:189px"><h4>Duis autem vel</h4><a>Typi non haben</a><a>Contact Us</a><a>Help</a><a>Privacy Policy</a><a>Terms Of Service</a></div>
  <div class="abs fcol" style="left:314px"><h4>Typi non haben</h4><a>Typi non haben</a><a>Contact Us</a><a>Help</a><a>Privacy Policy</a><a>Terms Of Service</a></div>
  <div class="abs newsletter"><h4>Newsletter</h4><p>Stay in touch with us by signing up for our quarterly newsletter!</p></div>
  <div class="abs field"></div>
  <div class="abs subscribe">SUBSCRIBE</div>
  <div class="abs footer-base"></div>
  <p class="abs copy">Copyright ©2013. All Rights Reserved.</p>
  <div class="abs social"><i></i><i></i><i></i><i></i></div>
</footer>

</body>
</html>
```